Young, dynamic furniture company needs a new business card design

We require a new business card design for our modern furniture company which supplies furniture and appliances to the property and development market.
Oakridge Interiors has become one of the leading furniture & appliance suppliers to the property market withing London. With over 10 years experience, we have increased our business to supply not only private landlords and managing agents, but also property developers, housing associations and local councils.
We offer not only a complete range of furniture which includes beds, wardrobes, dining sets and sofas, but also a high quality, full delivery and assembly service to help you with all our furnishing needs.

Target Market(s)

Private landlords, estate agents, letting agents, property management companies

Industry/Entity Type

Business

Contact Information for Business Card

Name,
Title,
Address,
Mobile,
Telephone,
Fax, Website, email address

Font styles to use
Sans Serif

Colors
3176b5
0555a3
85abd2
cfdeed

Requirements
Must have
• All the above information for each of our staff, along with our logo

```html
<!DOCTYPE html>
<html lang="en">
<head>
<meta charset="utf-8">
<title>Oakridge Interiors – Business Card</title>
<link href="https://fonts.googleapis.com/css2?family=Lato:wght@400;700&display=swap" rel="stylesheet">
<style>
  :root {
    --blue: #3176b5;
    --blue-deep: #0555a3;
    --blue-light: #85abd2;
    --blue-pale: #cfdeed;
    --ink: #1a1a1a;
    --white: #ffffff;
    --backdrop: #3b3b3d;
  }
  html, body {
    margin: 0;
    padding: 0;
    width: 1200px;
    height: 900px;
    overflow: hidden;
    background: var(--backdrop);
    font-family: "Lato", sans-serif;
  }
  .canvas { position: relative; width: 1200px; height: 900px; }
  .card {
    position: absolute;
    width: 560px;
    height: 320px;
    background: var(--white);
    overflow: hidden;
    box-shadow: 0 14px 30px rgba(0,0,0,0.45);
  }
  .card-back { left: 590px; top: 70px; }
  .card-front { left: 60px; top: 470px; }

  .brand { display: flex; align-items: center; gap: 10px; }
  .brand-square { width: 22px; height: 22px; background: var(--blue); }
  .brand-name {
    font-weight: 700;
    font-size: 28px;
    letter-spacing: 1px;
    color: var(--ink);
    text-transform: uppercase;
  }
  .tagline {
    font-size: 11px;
    letter-spacing: 1.2px;
    color: var(--ink);
    text-transform: uppercase;
    margin-top: 4px;
  }

  /* back */
  .back-content {
    position: absolute; inset: 0;
    display: flex; flex-direction: column;
    align-items: center; justify-content: center;
  }
  .back-content .tagline { margin-left: 32px; }
  .back-web {
    margin-top: 34px;
    font-size: 15px;
    letter-spacing: 2px;
    color: var(--ink);
  }

  /* front */
  .front-wave { position: absolute; inset: 0; }
  .front-brand { position: absolute; left: 38px; top: 30px; }
  .front-brand .tagline { margin-left: 32px; }
  .address {
    position: absolute; left: 28px; top: 202px;
    color: var(--white); font-size: 15px; line-height: 1.3;
    font-style: normal;
  }
  .person {
    position: absolute; right: 30px; top: 196px;
    text-align: right; color: var(--white);
  }
  .person-name { font-size: 21px; line-height: 1.1; }
  .person-title { font-size: 13px; margin-bottom: 6px; }
  .contact-list { list-style: none; margin: 0; padding: 0; }
  .contact-list li {
    display: flex; justify-content: flex-end; align-items: center;
    gap: 8px; font-size: 12.5px; line-height: 1.3;
  }
  .contact-list svg { width: 12px; height: 12px; fill: var(--white); flex: none; }
</style>
</head>
<body>
<div class="canvas">

  <section class="card card-back">
    <div class="back-content">
      <div>
        <div class="brand">
          <span class="brand-square"></span>
          <span class="brand-name">Oakridge Interiors</span>
        </div>
        <div class="tagline">Trade Furniture Solutions</div>
      </div>
      <div class="back-web">www.trade.oakridge-int.co.uk</div>
    </div>
  </section>

  <section class="card card-front">
    <svg class="front-wave" viewBox="0 0 560 320" preserveAspectRatio="none">
      <path d="M150,186 C310,196 460,165 560,108 L560,120 C470,176 320,200 150,186 Z" fill="var(--blue-light)"/>
      <path d="M0,130 C110,175 230,195 330,193 C430,191 510,160 560,128 L560,320 L0,320 Z" fill="var(--blue)"/>
    </svg>

    <div class="front-brand">
      <div class="brand">
        <span class="brand-square"></span>
        <span class="brand-name">Oakridge Interiors</span>
      </div>
      <div class="tagline">Trade Furniture Solutions</div>
    </div>

    <address class="address">
      7B Fenwick Trade Park<br>Harlow Green, London
    </address>

    <div class="person">
      <div class="person-name">Daniel Hartley</div>
      <div class="person-title">Manager</div>
      <ul class="contact-list">
        <li>020 7946 0321
          <svg viewBox="0 0 24 24"><path d="M6.6 10.8a15 15 0 0 0 6.6 6.6l2.2-2.2a1 1 0 0 1 1-.25 11.4 11.4 0 0 0 3.6.6 1 1 0 0 1 1 1V20a1 1 0 0 1-1 1A17 17 0 0 1 3 4a1 1 0 0 1 1-1h3.5a1 1 0 0 1 1 1c0 1.25.2 2.450.6 3.6a1 1 0 0 1-.25 1z"/></svg>
        </li>
        <li>020 7946 0000
          <svg viewBox="0 0 24 24"><path d="M7 1h10a2 2 0 0 1 2 2v18a2 2 0 0 1-2 2H7a2 2 0 0 1-2-2V3a2 2 0 0 1 2-2zm0 3v14h10V4zm5 15.5a1 1 0 1 0 0 2 1 1 0 0 0 0-2z"/></svg>
        </li>
        <li>info@trade.oakridge-int.co.uk
          <svg viewBox="0 0 24 24"><path d="M2 5h20v14H2zm2 2v.5l8 5 8-5V7zm0 2.8V17h16V9.8l-8 5z"/></svg>
        </li>
        <li>www.trade.oakridge-int.co.uk
          <svg viewBox="0 0 24 24"><path d="M12 2a10 10 0 1 0 0 20 10 10 0 0 0 0-20zm-1 2.1V8H7.6A8 8 0 0 1 11 4.1zm2 0A8 8 0 0 1 16.4 8H13zM6.6 10H11v4H6.6a8 8 0 0 1 0-4zm6.4 0h4.4a8 8 0 0 1 0 4H13zm-5.4 6H11v3.9A8 8 0 0 1 7.6 16zm5.4 0h3.4a8 8 0 0 1-3.4 3.9z"/></svg>
        </li>
      </ul>
    </div>
  </section>

</div>
</body>
</html>
```